Brightwave Reach - Business Card

We need a business card for a Social Media Marketing company that specializes in online marketing for small businesses in Canada using common Social Media platforms such as Pixlora, Chatterly, Blinkpost & Quibber.

I have uploaded a copy of our logo which I would like utilized in the business card. We would like the business card to be modern yet classy design.

Our website is www.brightwavereach.ca

Industry/Entity Type

Marketing

Contact Information for Business Card

Email: info@brightwavereach.ca
Website: www.brightwavereach.ca
Telephone: 604-555-0193

Colors

Designer to choose colors to be used in the design.

Requirements
Must have
• Social Media icons on reverse
• Please add some designs with color.

```html
<!DOCTYPE html>
<html lang="en">
<head>
<meta charset="utf-8">
<title>Brightwave Reach – Business Card</title>
<link rel="stylesheet" href="https://fonts.googleapis.com/css2?family=Lato:wght@400;700;900&display=swap">
<style>
  :root {
    --backdrop: #4a4a4a;
    --card-dark: #262626;
    --card-dark-top: #3a3a3a;
    --card-light: #ffffff;
    --ink: #1e1e1e;
    --ink-soft: #3a3a3a;
    --logo-grey: #4d4d4d;
    --on-dark: #f2f2f2;
    --rule: #2a2a2a;
  }
  html, body {
    margin: 0;
    width: 1200px;
    height: 800px;
    overflow: hidden;
    background: var(--backdrop);
    font-family: "Lato", sans-serif;
  }
  .canvas {
    position: relative;
    width: 1200px;
    height: 800px;
  }
  .card {
    position: absolute;
    left: 290px;
    width: 620px;
    height: 354px;
    border-radius: 4px;
    box-shadow: 0 10px 24px rgba(0,0,0,0.3);
    box-sizing: border-box;
    overflow: hidden;
  }
  /* Reverse side */
  .card-back {
    top: 28px;
    background: linear-gradient(160deg, var(--card-dark-top) 0%, var(--card-dark) 60%);
    color: var(--on-dark);
  }
  .back-brand {
    position: absolute;
    left: 0; right: 0;
    top: 74px;
    text-align: center;
    font-weight: 900;
    font-size: 44px;
    line-height: 1;
    letter-spacing: 1px;
    text-transform: uppercase;
    color: var(--on-dark);
  }
  .back-brand span { display: block; }
  .social-row {
    position: absolute;
    left: 60px; right: 60px;
    bottom: 44px;
    display: flex;
    justify-content: space-between;
    list-style: none;
    margin: 0;
    padding: 0;
  }
  .social-item {
    display: flex;
    flex-direction: column;
    align-items: center;
    gap: 8px;
    width: 100px;
  }
  .social-square {
    width: 34px;
    height: 34px;
    border-radius: 6px;
    background: var(--on-dark);
  }
  .social-name {
    font-size: 13px;
    font-weight: 700;
    color: var(--on-dark);
    letter-spacing: 0.5px;
  }
  /* Front side */
  .card-front {
    top: 418px;
    background: var(--card-light);
    color: var(--ink);
  }
  .front-brand {
    position: absolute;
    left: 30px;
    top: 0; bottom: 0;
    width: 270px;
    display: flex;
    flex-direction: column;
    justify-content: center;
    align-items: center;
    text-align: center;
    font-weight: 900;
    font-size: 34px;
    line-height: 1;
    letter-spacing: 1px;
    text-transform: uppercase;
    color: var(--logo-grey);
  }
  .divider {
    position: absolute;
    left: 318px;
    top: 105px;
    width: 1px;
    height: 140px;
    background: var(--rule);
  }
  .contact {
    position: absolute;
    left: 350px;
    top: 108px;
  }
  .person-name {
    margin: 0;
    font-size: 26px;
    font-weight: 700;
    color: var(--ink);
  }
  .person-role {
    margin: 2px 0 18px;
    font-size: 16px;
    font-weight: 400;
    color: var(--ink-soft);
  }
  .contact-list {
    list-style: none;
    margin: 0;
    padding: 0;
  }
  .contact-list li {
    display: flex;
    align-items: center;
    gap: 12px;
    font-size: 18px;
    line-height: 24px;
    color: var(--ink);
  }
  .contact-list svg {
    width: 13px;
    height: 13px;
    fill: var(--ink-soft);
    flex: none;
  }
</style>
</head>
<body>
<main class="canvas">

  <section class="card card-back" aria-label="Card reverse">
    <div class="back-brand"><span>Brightwave</span><span>Reach</span></div>
    <ul class="social-row">
      <li class="social-item"><div class="social-square"></div><span class="social-name">Chatterly</span></li>
      <li class="social-item"><div class="social-square"></div><span class="social-name">Pixlora</span></li>
      <li class="social-item"><div class="social-square"></div><span class="social-name">Quibber</span></li>
      <li class="social-item"><div class="social-square"></div><span class="social-name">Blinkpost</span></li>
    </ul>
  </section>

  <section class="card card-front" aria-label="Card front">
    <div class="front-brand"><span>Brightwave</span><span>Reach</span></div>
    <div class="divider"></div>
    <div class="contact">
      <h1 class="person-name">Daniel Hartley</h1>
      <p class="person-role">Manager</p>
      <ul class="contact-list">
        <li>
          <svg viewBox="0 0 16 16" aria-hidden="true"><path d="M3.5 1.5l2.5 0 1.2 3.2-1.6 1.2c.8 1.8 2.2 3.2 4 4l1.2-1.6 3.2 1.2v2.5c0 .8-.7 1.5-1.5 1.5C6.6 13.5 2 8.9 2 3c0-.8.7-1.5 1.5-1.5z"/></svg>
          <span>604-555-0193</span>
        </li>
        <li>
          <svg viewBox="0 0 16 16" aria-hidden="true"><path d="M1 3h14v10H1z M2 4.2v.3l6 4 6-4v-.3z" fill-rule="evenodd"/></svg>
          <span>info@brightwavereach.ca</span>
        </li>
        <li>
          <svg viewBox="0 0 16 16" aria-hidden="true"><circle cx="8" cy="8" r="7"/><path d="M1 8h14M8 1c-2.5 2-2.5 12 0 14M8 1c2.5 2 2.5 12 0 14" stroke="#fff" stroke-width="1" fill="none"/></svg>
          <span>www.brightwavereach.ca</span>
        </li>
      </ul>
    </div>
  </section>

</main>
</body>
</html>
```